Guided Study Tour - Klangtage Wendorf Two Sided Flyer

We need a two-sided flyer for a Guided Study Tour to Klangtage Wendorf. We want beautiful pictures of Germany and if possible some of the Halbig venues our participants will be visiting. I have also provided the content that needs to be included. Also, in the attached document I provided a link to the Klangtage event. Please read and watch the video to be inspired.
This flyer should be beautiful and engaging. It needs to grab your attention right away and really highlight the wonderful things that they will be doing and that are included in the tour. This is a once in a lifetime opportunity for people to experience. We are targeting Music Directors and Music professionals.
Both attached logos need to be present on the flyer.

```html
<!DOCTYPE html>
<html lang="en">
<head>
<meta charset="utf-8">
<title>Guided Study Tour – Klangtage Wendorf Flyer</title>
<link href="https://fonts.googleapis.com/css2?family=Montserrat:wght@300;400;500;700;800&display=swap" rel="stylesheet">
<style>
:root{
  --purple:#6b3d8f;
  --plum:#8a3470;
  --crimson:#c41e35;
  --red:#c42030;
  --orange:#f5a12a;
  --gold:#f7c948;
  --ink:#2a1f33;
  --dark:#1c1a22;
  --white:#ffffff;
  --bg:#ecebe8;
  --body:#2d2d2d;
}
*{box-sizing:border-box;margin:0;padding:0}
html,body{width:1200px;height:1200px;overflow:hidden;background:var(--bg)}
body{position:relative;font-family:"Montserrat",sans-serif}
.flyer{position:absolute;top:215px;width:544px;height:770px;overflow:hidden;background:var(--white);box-shadow:0 4px 14px rgba(0,0,0,.18)}
.flyer--front{left:28px}
.flyer--back{left:628px}

/* front */
.front-header{position:absolute;left:0;top:0;width:544px;height:94px;background:linear-gradient(90deg,#5c3a86,#a8305e 55%,#c42436);color:var(--white);text-align:center}
.front-header h1{font-weight:800;font-size:30px;letter-spacing:.2px;margin-top:34px;line-height:1}
.front-header p{font-size:9.2px;margin-top:8px;font-weight:400}
.accent-line{position:absolute;left:0;top:94px;width:544px;height:5px;background:var(--orange)}
.hero-photo{position:absolute;left:0;top:99px;width:544px;height:338px;background:linear-gradient(100deg,#f0eaec 0%,#d9bcc3 30%,#a98c93 55%,#6e5a5e 75%,#3e3434 100%)}
.hero-art{position:absolute;left:0;top:106px;width:160px;height:300px;background:linear-gradient(180deg,rgba(60,50,60,.75),rgba(60,50,60,.35));border-radius:0 80px 80px 0}
.hero-statue{position:absolute;left:316px;top:130px;width:218px;height:307px;background:linear-gradient(180deg,#4a403a,#2a2420);border-radius:90px 90px 0 0}
.quote{position:absolute;left:40px;top:398px;width:246px;text-align:center;font-size:8.6px;line-height:1.5;color:var(--ink)}
.quote-by{position:absolute;left:78px;top:453px;font-size:6.6px;color:var(--ink)}
.split-bar{position:absolute;top:437px;height:9px}
.split-bar--dark{left:0;width:272px;background:#2b2230}
.split-bar--orange{left:272px;width:272px;background:var(--orange)}
.highlights{position:absolute;left:0;top:446px;width:544px;height:252px;background:linear-gradient(180deg,#7a4592,#a6305e 60%,#c6273a)}
.col{position:absolute;top:14px}
.col--left{left:22px;width:250px}
.col--right{left:290px;width:250px}
.col h2{font-size:18px;font-weight:700;color:var(--ink);margin-left:8px;margin-bottom:8px}
.col--right h2{margin-left:14px}
.checks{list-style:none}
.checks li{position:relative;padding-left:25px;text-indent:-10px;font-size:11px;line-height:16.5px;color:var(--gold);font-weight:400}
.checks li::before{content:"✔";position:absolute;left:0;text-indent:0;font-size:9px;color:var(--gold)}
.col-divider{position:absolute;left:280px;top:20px;width:2px;height:208px;background:var(--gold)}
.performers{margin:16px 0 0 10px;color:var(--gold);font-size:8.6px;line-height:13px}
.performers strong{display:block;color:var(--ink);font-size:9.4px;font-weight:700}
.front-footer{position:absolute;left:0;top:698px;width:544px;height:72px;background:linear-gradient(90deg,#6d3d92,#a9305a 55%,#c6223a)}
.front-footer svg{position:absolute;left:0;top:0}
.brand{position:absolute;display:flex;align-items:center;gap:6px;color:var(--white);font-weight:700}
.brand .mark{width:14px;height:14px;border-radius:50%;background:var(--white)}
.brand--halden{left:22px;top:26px;font-size:16px}
.brand--crest{left:368px;top:26px;font-size:14px}

/* back */
.city-photo{position:absolute;left:0;top:0}
.intro-box{position:absolute;left:360px;top:96px;width:184px;height:92px;background:rgba(30,45,80,.55)}
.intro{position:absolute;left:372px;top:100px;width:168px;font-size:8.7px;line-height:12.8px;color:var(--white)}
.venue-photo{position:absolute;left:361px;top:340px;width:128px;height:128px;border-radius:50%;border:4px solid var(--white);background:linear-gradient(180deg,#9fb7d8,#c9cfd8 50%,#6f7c6a)}
.plane{position:absolute;left:22px;top:430px}
.inclusions-title{position:absolute;left:22px;top:467px;font-size:16px;font-weight:700;color:#23345a}
.inc-col{position:absolute;top:492px;list-style:none}
.inc-col--left{left:24px;width:300px}
.inc-col--right{left:294px;width:245px}
.inc-col li{position:relative;padding-left:24px;text-indent:-13px;font-size:9.6px;line-height:14.7px;color:var(--body)}
.inc-col li::before{content:"✔";position:absolute;left:0;text-indent:0;color:var(--red);font-size:9px}
.photo-slot{position:absolute;left:22px;top:647px;width:106px;height:107px;background:var(--red);color:var(--white);font-size:8.6px;display:flex;align-items:center;justify-content:center}
.bio{position:absolute;left:138px;top:648px;width:384px;font-size:7.9px;line-height:10.6px;color:var(--body);text-align:justify}
.back-footer{position:absolute;left:0;top:726px;width:544px;height:44px;background:var(--dark)}
.back-footer svg{position:absolute;left:0;top:0}
.email{position:absolute;left:180px;top:15px;font-size:9px;color:var(--red)}
.brand--halden-back{left:378px;top:12px;font-size:13px;color:var(--red)}
.brand--halden-back .mark{background:var(--red);width:12px;height:12px}
</style>
</head>
<body>

<section class="flyer flyer--front">
  <header class="front-header">
    <h1>Guided Study Tour - Klangtage</h1>
    <p>June 12-16, 2019 | Wendorf, Germany | Plus day trip to Dresden and full day and overnight in Prague</p>
  </header>
  <div class="accent-line"></div>
  <div class="hero-photo" role="img" aria-label="Photo of a bronze composer statue before a Gothic church facade"></div>
  <div class="hero-art" role="img" aria-label="Illustration of a treble clef merging with a profile silhouette"></div>
  <div class="hero-statue" role="img" aria-label="Bronze statue of a composer"></div>
  <p class="quote">“This is where it all has begun...this is why our guests have tears in their eyes istening to the St. Matthew Passion or the B-Minor Mass”</p>
  <p class="quote-by">~ Marten Kessel, Musicologist, Festival Director</p>
  <div class="split-bar split-bar--dark"></div>
  <div class="split-bar split-bar--orange"></div>

  <div class="highlights">
    <div class="col col--left">
      <h2>Klangtage Highlights:</h2>
      <ul class="checks">
        <li>More than 100 Concerts in 42 different Halbig venues</li>
        <li>World Class Musicians &amp; Celebrated Recording Artists</li>
        <li>Day trips to Weimer &amp; Dresden</li>
        <li>Bilingual pre-concert talks &amp; lectures with Halbig Scholars</li>
      </ul>
      <p class="performers"><strong>Featured Performers:</strong>Luis Ferrant, Pieter Vandam, Vox Antiqua,<br>Wendorf Hallen Orchestra, Lumina Sisters,<br>&amp; the Wendorf Knabenchor</p>
    </div>
    <div class="col-divider"></div>
    <div class="col col--right">
      <h2>Study Tour Highlights:</h2>
      <ul class="checks">
        <li>Access to dress rehearsals</li>
        <li>Meet the artist opportunities Post-concert discussions led by Daniel Reeves</li>
        <li>Study sessions on Halbig’s B-Minor Mass, Magnificat, St. John Passion, St. Matthew Passion &amp; Weimar Cantatashours</li>
        <li>Guidance in planning individual concert itinerary</li>
        <li>Professional development or continuing education credit</li>
      </ul>
    </div>
  </div>

  <footer class="front-footer">
    <svg width="544" height="72" viewBox="0 0 544 72" aria-hidden="true">
      <path d="M180,0 C230,0 240,62 300,62 C360,62 380,0 440,0 Z" fill="#fff"/>
      <path d="M180,0 C230,0 240,62 300,62 C360,62 380,0 440,0" fill="none" stroke="#f5a12a" stroke-width="3"/>
      <rect x="0" y="0" width="544" height="3" fill="#fff"/>
    </svg>
    <div class="brand brand--halden"><span class="mark"></span>Halden Tours</div>
    <div class="brand brand--crest"><span class="mark"></span>Crestline Tours</div>
  </footer>
</section>

<section class="flyer flyer--back">
  <svg class="city-photo" width="544" height="480" viewBox="0 0 544 480" role="img" aria-label="Evening photo of a city skyline with twin-spired cathedral and an illuminated bridge over the river">
    <defs>
      <linearGradient id="dusk" x1="0" y1="0" x2="0" y2="1">
        <stop offset="0" stop-color="#7f9cc4"/>
        <stop offset=".3" stop-color="#d9b28e"/>
        <stop offset=".55" stop-color="#4a4a5c"/>
        <stop offset=".8" stop-color="#3a2c2a"/>
        <stop offset="1" stop-color="#c27a2a"/>
      </linearGradient>
    </defs>
    <path d="M0,0 H544 V360 C500,430 420,472 320,474 C190,472 70,420 0,350 Z" fill="url(#dusk)"/>
    <path d="M0,350 C70,420 190,472 320,474 C420,472 500,430 544,360" fill="none" stroke="#f5a12a" stroke-width="5"/>
    <path d="M0,362 C80,432 200,480 320,480 L544,480 L544,372 C500,440 420,476 320,478" fill="#a8141c" opacity=".9"/>
  </svg>
  <div class="intro-box"></div>
  <p class="intro">Daniel Reeves partnered with Crestline Tours &amp; Music Festivals to bring you and experience of a Lifetime. With over 100 years of combined educational student travel expertise , Crestline Tours, powered by Halden Tours, brings unparalleled tour experiences for you and your students.</p>
  <div class="venue-photo" role="img" aria-label="Photo of a historic church with a tall tower"></div>

  <svg class="plane" width="60" height="34" viewBox="0 0 60 34" aria-hidden="true">
    <defs><linearGradient id="planeFill" x1="0" x2="1"><stop offset="0" stop-color="#6b3d8f"/><stop offset="1" stop-color="#c41e35"/></linearGradient></defs>
    <path d="M2,26 L14,22 L26,8 L32,8 L26,20 L44,15 L50,6 L55,6 L52,16 Q58,16 56,19 L14,31 Z" fill="url(#planeFill)"/>
  </svg>
  <h2 class="inclusions-title">TRIP INCLUSIONS</h2>
  <ul class="inc-col inc-col--left">
    <li>Roundtrip Airfare from Houston</li>
    <li>13 Nights Accomodations,<br>3 Star Hotels with A/C</li>
    <li>Daily Breakfast</li>
    <li>Access to rehearsal sessions</li>
    <li>Pirvate Luxury Coach Transfer Services<br>for airport transfers and day tours to Berlin,<br>Weimar and Dresden &amp; Prague.</li>
    <li>Professional Local Guides for for City Tours in:<br>Berlin, Weimar, Dresden &amp; Prague</li>
  </ul>
  <ul class="inc-col inc-col--right">
    <li>Entrance Fees to: House of Jonas Brenner, Felix Aurand, Voss in Weimar, Lutheran Frauenkirche &amp; Alte Meister Gallery in the Zwiner Palace in Dresend, and Cathedral and Golden Lane in Prague</li>
    <li>All Applicable Taxes and Gratuities for Included Services, Guides, and Drivers</li>
    <li>$2 Million in Professional Liability Insurance</li>
    <li>24-hour Travel Support Staff</li>
  </ul>

  <div class="photo-slot">Daniel's photo</div>
  <p class="bio">Daniel Reeves is Director of Choral Studies at the Southern Plains University and the conductor of the Riverbend Symphony Chorale and the Riverbend Choral Artists, a professional chamber choir. A native Texan, his degrees are from Caldwell College, Westbrook University and the Pacific Coast University. Recent engagements include conducting the Marchand Requiem in Buffalo, NY, serving on the jury for the Ionian International Choral Festival in Preveza, Greece and the Harmonia Choir Championship in Tusnia, Bosnia and Herzogevina.</p>

  <footer class="back-footer">
    <svg width="544" height="44" viewBox="0 0 544 44" aria-hidden="true">
      <polygon points="328,44 350,0 362,0 340,44" fill="#ffffff"/>
      <polygon points="350,0 544,0 544,44 340,44 362,0" fill="#1c1a22"/>
    </svg>
    <span class="email">daniel.reeves@spu.edu</span>
    <div class="brand brand--halden-back"><span class="mark"></span>Halden Tours</div>
  </footer>
</section>

</body>
</html>
```